TeaLantern Flyer

I require an A5 sized flyer to be designed that advertised the new flexible workspace of TeaLantern.
should say it is a "Flexible Workspace with EV Charging"
web address is www.tealantern.co.uk
It should show the 3 different types of membership as priced on the website

```html
<!DOCTYPE html>
<html lang="en">
<head>
<meta charset="utf-8">
<title>TeaLantern Flyer</title>
<link href="https://fonts.googleapis.com/css2?family=Archivo+Black&family=Poppins:wght@400;500;600;700&display=swap" rel="stylesheet">
<style>
  :root {
    --orange: #f28c00;
    --ink: #2b2b2b;
    --charcoal: #2e2e2e;
    --day: #8a9ee0;
    --light: #4467dd;
    --white: #ffffff;
    --stage: #ececec;
    --body-text: #3a3a3a;
  }
  * { box-sizing: border-box; margin: 0; padding: 0; }
  html, body { width: 1200px; height: 2857px; overflow: hidden; }
  body { background: var(--stage); font-family: "Poppins", sans-serif; position: relative; }

  .flyer {
    position: absolute; left: 60px; top: 662px;
    width: 1080px; height: 1532px;
    background: var(--white);
    box-shadow: 0 10px 30px rgba(0,0,0,0.25);
    overflow: hidden;
  }
  .abs { position: absolute; }

  .hero-photo {
    left: 650px; top: 0; width: 430px; height: 489px;
    background: linear-gradient(135deg, #5a5f68 0%, #d9dbde 45%, #f4f4f4 60%, #3c3f45 100%);
    border-bottom-right-radius: 90px;
    z-index: 1;
  }
  .brand-name {
    left: 93px; top: 78px;
    font-family: "Archivo Black", sans-serif;
    font-size: 74px; line-height: 1; color: var(--ink);
    z-index: 2;
  }
  .headline {
    left: 93px; top: 200px;
    font-family: "Archivo Black", sans-serif;
    font-size: 76px; line-height: 0.98; color: var(--ink);
    z-index: 2;
  }
  .headline-band {
    left: 93px; top: 359px; width: 739px; height: 152px;
    background: var(--orange);
    padding: 14px 0 0 28px;
    font-family: "Archivo Black", sans-serif;
    font-size: 62px; line-height: 0.98; color: var(--white);
    z-index: 0;
  }
  .headline-band-text {
    left: 121px; top: 373px;
    font-family: "Archivo Black", sans-serif;
    font-size: 62px; line-height: 0.98; color: var(--white);
    z-index: 2;
  }

  .dark-band { left: 0; top: 766px; width: 1080px; height: 156px; background: var(--charcoal); }
  .space-photo {
    top: 541px; width: 440px; height: 304px;
    border: 3px solid var(--white);
    box-shadow: 0 0 0 1px #cfcfcf;
  }
  .space-photo.lounge-kitchen { left: 93px; background: linear-gradient(160deg, #e9ecef 0%, #b9bec4 55%, #6d625a 100%); }
  .space-photo.lounge-seating { left: 551px; background: linear-gradient(160deg, #eef0f2 0%, #a9adb3 50%, #6a4a34 100%); }

  .caption { left: 0; top: 848px; width: 1080px; text-align: center; font-size: 19px; line-height: 1.3; }
  .caption .lead { color: var(--orange); }
  .caption .rest { color: var(--white); font-weight: 600; }

  .section-title {
    left: 0; top: 955px; width: 1080px; text-align: center;
    font-weight: 700; font-size: 27px; color: var(--ink);
  }

  .plan-body {
    top: 1092px; width: 302px; height: 319px;
    border: 1.5px solid; background: var(--white);
  }
  .plan-head {
    top: 997px; width: 277px; height: 96px;
    color: var(--white); text-align: center;
    font-weight: 700; font-size: 22px;
    padding-top: 16px;
  }
  .plan-head svg { display: block; margin: 0 auto 6px; }

  .plan--day .plan-head { left: 93px; background: var(--day); }
  .plan--day .plan-body { left: 80px; border-color: var(--day); }
  .plan--light .plan-head { left: 400px; background: var(--light); }
  .plan--light .plan-body { left: 388px; border-color: var(--light); }
  .plan--all .plan-head { left: 708px; background: var(--orange); }
  .plan--all .plan-body { left: 696px; border-color: var(--orange); }

  .features { list-style: none; padding: 18px 10px 0 24px; font-size: 13.5px; line-height: 1.5; color: var(--body-text); }
  .features li { position: relative; padding-left: 20px; }
  .features li::before {
    content: ""; position: absolute; left: 2px; top: 4px;
    width: 5px; height: 9px;
    border-right: 2px solid; border-bottom: 2px solid;
    transform: rotate(40deg);
  }
  .features li .note { display: block; }
  .plan--day .features li::before { border-color: var(--day); }
  .plan--light .features li::before { border-color: var(--light); }
  .plan--all .features li::before { border-color: var(--orange); }
  .plan--all .features { font-size: 12.5px; line-height: 1.32; padding: 14px 4px 0 14px; }
  .plan--all .features li { white-space: nowrap; }

  .price {
    position: absolute; left: 0; width: 100%; text-align: center;
    color: var(--ink); font-size: 19px; line-height: 1.1;
  }
  .price strong { font-weight: 700; font-size: 31px; }
  .plan--day .price { top: 200px; }
  .plan--light .price { top: 170px; }
  .plan--all .price { top: 208px; }
  .price-tag {
    position: absolute; left: 50%; transform: translateX(-50%);
    top: 254px; width: 172px; height: 46px; border-radius: 12px;
    color: var(--white); font-size: 12.5px; line-height: 1.15;
    display: flex; align-items: center; justify-content: center; text-align: center;
  }
  .plan--day .price-tag { background: var(--day); }
  .plan--light .price-tag { background: var(--light); }
  .plan--all .price-tag { background: var(--orange); }

  .footer-line { left: 0; top: 1520px; width: 1080px; height: 12px; background: var(--charcoal); }
  .footer-tab { left: 290px; top: 1474px; }
  .footer-url {
    left: 290px; top: 1484px; width: 500px; text-align: center;
    color: var(--white); font-size: 23px; letter-spacing: 2px;
  }
</style>
</head>
<body>
  <main class="flyer">
    <div class="abs headline-band"></div>
    <div class="abs hero-photo" role="img" aria-label="Photo of an EV charging point beside a white electric car parked outside the office building"></div>
    <div class="abs brand-name">TeaLantern</div>
    <h1 class="abs headline">FLEXIBLE<br>WORKSPACE</h1>
    <div class="abs headline-band-text">WITH<br>EV CHARGING</div>

    <div class="abs dark-band"></div>
    <div class="abs space-photo lounge-kitchen" role="img" aria-label="Photo of the open-plan workspace with kitchen and bar seating"></div>
    <div class="abs space-photo lounge-seating" role="img" aria-label="Photo of the lounge area with leather sofas and desk pods"></div>
    <p class="abs caption">
      <span class="lead">Unique workspace environment for EV owners looking to</span><br>
      <span class="rest">recharge their Electric Vehicles, grab a snack and beverage, and catch up with some office work.</span>
    </p>

    <h2 class="abs section-title">OUR 3 DIFFERENT TYPES OF MEMBERSHIP</h2>

    <section class="plan plan--day">
      <div class="abs plan-head">
        <svg width="34" height="28" viewBox="0 0 34 28" fill="none" stroke="#fff" stroke-width="2.2"><rect x="2" y="7" width="30" height="19" rx="2"/><path d="M12 7V3h10v4M2 15h30M15 15v3h4v-3"/></svg>
        DAY MEMBER
      </div>
      <div class="abs plan-body">
        <ul class="features">
          <li>Use of Hot Desks &amp; Lounge Areas</li>
          <li>Secure Wifi</li>
          <li>Free Tea &amp; Coffee</li>
        </ul>
        <div class="price"><strong>£25.00</strong><br>EACH VISIT</div>
        <div class="price-tag">Price Inclusive of VAT<br>Each Visit</div>
      </div>
    </section>

    <section class="plan plan--light">
      <div class="abs plan-head">
        <svg width="30" height="30" viewBox="0 0 30 30" fill="none" stroke="#fff" stroke-width="2.2"><circle cx="14" cy="16" r="11"/><circle cx="14" cy="16" r="6"/><circle cx="14" cy="16" r="1.5" fill="#fff"/><path d="M14 16L26 4M22 4h4v4"/></svg>
        LIGHT MEMBER
      </div>
      <div class="abs plan-body">
        <ul class="features">
          <li>Use of Hot Desks &amp; Lounge Areas</li>
          <li>Secure Wifi</li>
          <li>Free Tea &amp; Coffee</li>
          <li>Discounted E/V Charge Rates</li>
          <li>Access to Meeting Rooms <span class="note">(£10+vat per person, per hour)</span></li>
        </ul>
        <div class="price"><strong>£18</strong> A MONTH<br><strong>+ £18</strong> EACH VISIT</div>
        <div class="price-tag">Price Inclusive of VAT<br>Per month</div>
      </div>
    </section>

    <section class="plan plan--all">
      <div class="abs plan-head">
        <svg width="32" height="28" viewBox="0 0 32 28" fill="none" stroke="#fff" stroke-width="2.2" stroke-linejoin="round"><path d="M8 2h16l6 8-14 16L2 10z"/><path d="M2 10h28M12 2l-4 8 8 16 8-16-4-8"/></svg>
        ALL ACCESS MEMBER
      </div>
      <div class="abs plan-body">
        <ul class="features">
          <li>Unlimited Number of Visits Each Month</li>
          <li>Dedicated Desk <span class="note">(lockable draws + £60 a month)</span></li>
          <li>Receptionist to Meet &amp; Greet Guests</li>
          <li>Use of Lounge Areas</li>
          <li>Secure Wifi</li>
          <li>Free Tea &amp; Coffee</li>
          <li>Discounted E/V Charge Rates</li>
          <li>Access to Meeting Rooms <span class="note">(£10+vat per person, per hour)</span></li>
        </ul>
        <div class="price"><strong>£180.00</strong></div>
        <div class="price-tag">Price Inclusive of VAT<br>Per month</div>
      </div>
    </section>

    <div class="abs footer-line"></div>
    <svg class="abs footer-tab" width="500" height="58" viewBox="0 0 500 58"><path d="M0 58 C20 58 22 0 50 0 H450 C478 0 480 58 500 58 Z" fill="#2e2e2e"/></svg>
    <div class="abs footer-url">www.tealantern.co.uk</div>
  </main>
</body>
</html>
```